Willow Cradle Pregnancy and Baby Massage

I need a web design for a new business, WILLOW CRADLE PREGNANCY AND BABY MASSAGE that I am in the process of setting up in the suburbs of Perth, Western Australia. The business is owned and operated by myself and my intention is to service Pregnant Mothers and Parents of Young Babies that would benefit from massage. I would like to have a "Home Page" and pages for "About Me", "Pregnancy Massage", "Baby Massage", a Pricing Page for Pregnancy Massage Sessions, a Pricing Page for Baby Massage Sessions, and a "Contact Me" page to allow clients to either contact me with queries or book available pregnancy massage sessions on a particular day of the week. I would also like a "News" page that would include articles I have written, news about new courses and a link to my Facebook page (yet to be set up). I would like to keep the colour schemes similar to my logo design colours. I need the design to be easy to follow and to appeal to a younger audience (20's to mid 30's).
The target audience is pregnant mothers-to-be wishing to receive massage treatments, and new parents and grandparents of small babies that would like to learn how to massage their babies.
The look and feel should be modern, professional, elegant and feminine.
I need the design to be in a standard format such that I can update the content by myself ( and does not need specialised software) as the company and business progresses.

Target Market(s)

Contact Information for Business Card

Card should have rounded edges. Design should have the same "feel" as the website. Contact Details of my business address, mobile phone, email and website should be included.

Font styles to use
Script

Requirements
Must have
• Same colours as logo design. In cmyk system, the colours are: 20,60,0,0 which best result is pantone 681 and 40,40,0,0 which best result is pantone 2645. Card should include the logo design.

```html
<!DOCTYPE html>
<html lang="en">
<head>
<meta charset="utf-8">
<title>Contact Me – Willow Cradle Pregnancy and Baby Massage</title>
<link rel="stylesheet" href="https://fonts.googleapis.com/css2?family=Questrial&family=Open+Sans:wght@400&display=swap">
<style>
  :root{
    --nav-bg:#3d3b40;
    --nav-text:#d9d6de;
    --pink:#b8679f;
    --purple:#7b73ad;
    --lilac:#b7a2cb;
    --lavender:#c4bfdc;
    --blush:#e6c6dc;
    --text:#3a3a3a;
    --field-border:#c9c9c9;
    --footer-band:#f6e9ef;
    --footer-bar:#4e4570;
    --footer-text:#e8e4f0;
    --white:#ffffff;
  }
  *{box-sizing:border-box;margin:0;padding:0}
  html,body{width:1200px;height:1163px;overflow:hidden;background:var(--white)}
  body{font-family:"Questrial",sans-serif;color:var(--text);position:relative}
  .site-header{position:absolute;top:0;left:0;width:1200px;height:190px}
  .nav-bar{position:absolute;top:0;left:0;width:1200px;height:41px;background:var(--nav-bg)}
  .main-nav{position:absolute;right:133px;top:0;height:41px;display:flex;gap:27px;align-items:center}
  .main-nav a{color:var(--nav-text);text-decoration:none;font-size:13px}
  .main-nav a.current{color:var(--white);text-decoration:underline;text-underline-offset:3px}
  .waves{position:absolute;top:41px;left:0}
  .brand-card{position:absolute;left:132px;top:0;width:283px;height:179px;background:var(--white);
    border-radius:0 0 26px 26px;box-shadow:0 4px 10px rgba(0,0,0,.22);z-index:2}
  .brand-card .stitch{position:absolute;left:8px;right:8px;top:0;bottom:9px;border:1.5px dashed #555;border-top:none;border-radius:0 0 20px 20px}
  .brand-name{position:absolute;left:0;right:0;top:58px;text-align:center;color:var(--pink);font-size:24px;line-height:1.25}
  .brand-name .dot{display:block;width:40px;height:40px;border-radius:50%;background:var(--pink);margin:-48px auto 10px}
  .contact-info{position:absolute;top:268px;left:0;width:1200px;text-align:center}
  h1,h2{color:var(--pink);font-weight:400}
  h1{font-size:30px}
  .intro{font-size:17.5px;margin-top:20px}
  .owner{font-size:17px;margin-top:23px}
  .business{font-family:"Open Sans",sans-serif;font-size:13px;margin-top:3px}
  .phone{color:var(--purple);font-size:19px;margin-top:20px}
  .contact-form{position:absolute;top:534px;left:132px;width:935px;text-align:center}
  .contact-form h2{font-size:30px}
  .field-row{display:flex;gap:21px;margin-top:25px}
  .field{height:41px;border:1px solid var(--field-border);font-family:inherit;font-size:12px;padding:0 15px;color:#555;flex:1}
  .field.message{width:100%;margin-top:23px;display:block}
  .submit{display:inline-block;margin-top:23px;width:80px;height:41px;background:var(--pink);color:var(--white);border:none;font-family:inherit;font-size:14px}
  .footer-band{position:absolute;top:843px;left:0;width:1200px;height:208px;
    background:radial-gradient(circle at 75% 40%,#f3d2e0 0,transparent 40%),radial-gradient(circle at 5% 90%,#f2c8da 0,transparent 25%),var(--footer-band)}
  .cert-badge{position:absolute;left:142px;top:35px;width:255px;height:145px;border-radius:10px;background:#ead3e5}
  .follow{position:absolute;right:133px;top:78px;text-align:center;font-size:16px}
  .follow .social{display:block;width:42px;height:42px;border-radius:50%;background:var(--footer-bar);margin:10px auto 0}
  .footer-bar{position:absolute;top:1051px;left:0;width:1200px;height:112px;background:var(--footer-bar);
    font-family:"Open Sans",sans-serif;color:var(--footer-text);text-align:center;font-size:12.5px}
  .footer-nav{margin-top:32px}
  .footer-nav a{color:var(--footer-text);text-decoration:none}
  .footer-nav .sep{margin:0 9px}
  .copyright{margin-top:14px}
</style>
</head>
<body>
<header class="site-header">
  <div class="nav-bar">
    <nav class="main-nav">
      <a href="#">Home</a><a href="#">About Me</a><a href="#">Pregnancy Massage</a><a href="#">Baby Massage</a><a href="#">Pricing</a><a href="#">News</a><a href="#" class="current">Contact Me</a>
    </nav>
  </div>
  <svg class="waves" width="1200" height="150" viewBox="0 0 1200 150" aria-hidden="true">
    <path d="M0 0 H1200 V150 C1100 95 1000 60 850 45 C700 35 500 120 300 108 C180 100 80 130 0 124 Z" fill="var(--blush)"/>
    <path d="M0 0 H1200 V80 C1080 30 950 10 800 30 C650 55 560 110 420 108 C280 106 120 40 0 20 Z" fill="var(--lavender)"/>
    <path d="M0 0 H1200 V50 C1120 25 1020 8 900 15 C760 25 640 90 520 92 C400 95 250 45 130 40 C70 38 30 25 0 20 Z" fill="var(--lilac)" opacity=".85"/>
  </svg>
  <div class="brand-card">
    <div class="stitch"></div>
    <div class="brand-name"><span class="dot"></span>Willow Cradle<br>Pregnancy and Baby Massage</div>
  </div>
</header>

<main>
  <section class="contact-info">
    <h1>Contact Me</h1>
    <p class="intro">To contact Rosalind, or to book a session, please use the details below, or submit the contact form.</p>
    <p class="owner">Rosalind Hart</p>
    <p class="business">Willow Cradle Pregnancy and Infant Massage</p>
    <p class="phone">Telephone : 040 0555 217</p>
  </section>

  <form class="contact-form">
    <h2>Contact Form</h2>
    <div class="field-row">
      <input class="field" type="text" placeholder="Name">
      <input class="field" type="email" placeholder="Email">
      <input class="field" type="tel" placeholder="Phone">
    </div>
    <input class="field message" type="text" placeholder="Message">
    <button class="submit" type="button">SUBMIT</button>
  </form>
</main>

<footer>
  <div class="footer-band" role="img" aria-label="Soft pink background scattered with floating hearts">
    <div class="cert-badge" role="img" aria-label="Certification badge"></div>
    <div class="follow">Follow us on<span class="social" role="img" aria-label="Social page link"></span></div>
  </div>
  <div class="footer-bar">
    <nav class="footer-nav">
      <a href="#">Home</a><span class="sep">|</span><a href="#">About Me</a><span class="sep">|</span><a href="#">Pregnancy Massage</a><span class="sep">|</span><a href="#">Baby Massage</a><span class="sep">|</span><a href="#">Pricing</a><span class="sep">|</span><a href="#">News</a><span class="sep">|</span><a href="#">Contact Me</a>
    </nav>
    <p class="copyright">Copyright &copy; 2017 Willow Cradle Pregnancy &amp; Baby Massage. All rights reserved.</p>
  </div>
</footer>
</body>
</html>
```